Carpet cleaning company focused on high quality needs business cards

We are a growing company that just merged with another company and need to design a new business card. We do both residential as well as commercial cleaning. We do carpet, tile & grout, upholstery, hard floors, and stain & pet odor removal. We treat our customers like family and strive to achieve outstanding results with every job.

```html
<!DOCTYPE html>
<html lang="en">
<head>
<meta charset="utf-8">
<title>Ray's Fresh Fiber Cleaning – Business Card</title>
<link href="https://fonts.googleapis.com/css2?family=Montserrat:wght@400;500;700;800&family=Oswald:wght@500;600&display=swap" rel="stylesheet">
<style>
  :root {
    --page-bg: #2e2f31;
    --card-white: #ffffff;
    --ray-grey: #eceef0;
    --brand-blue: #1a7fc4;
    --brand-blue-deep: #0b5fa6;
    --brand-blue-light: #3a9ad6;
    --accent-red: #f04a3f;
    --ink: #1c1c1c;
    --ink-soft: #333333;
    --mascot-tan: #c59a5a;
  }
  * { box-sizing: border-box; margin: 0; padding: 0; }
  html, body { width: 1200px; height: 1200px; overflow: hidden; }
  body {
    background: var(--page-bg);
    font-family: "Montserrat", sans-serif;
    position: relative;
  }
  .card {
    position: absolute;
    left: 150px;
    width: 900px;
    height: 514px;
    border-radius: 34px;
    overflow: hidden;
  }
  /* ---------- front ---------- */
  .card-front {
    top: 50px;
    background: radial-gradient(circle at 58% 48%, var(--card-white) 0%, var(--ray-grey) 70%, var(--card-white) 100%);
  }
  .front-mascot {
    position: absolute;
    left: 560px;
    top: 40px;
    width: 280px;
    height: 290px;
    background: linear-gradient(160deg, var(--brand-blue) 0%, var(--brand-blue) 45%, var(--accent-red) 46%, var(--accent-red) 100%);
    border-radius: 6px;
  }
  .contact {
    position: absolute;
    left: 56px;
    top: 250px;
  }
  .contact-name {
    font-weight: 700;
    font-size: 42px;
    color: var(--brand-blue);
    letter-spacing: 0.5px;
    line-height: 1;
  }
  .contact-title {
    font-size: 20px;
    color: var(--ink-soft);
    margin: 4px 0 16px;
    letter-spacing: 1px;
  }
  .contact-list { list-style: none; }
  .contact-list li {
    display: flex;
    align-items: center;
    gap: 12px;
    font-size: 19px;
    color: var(--ink);
    margin-bottom: 8px;
  }
  .contact-list svg { width: 22px; height: 22px; fill: var(--brand-blue); flex: none; }
  .services-label {
    position: absolute;
    right: 290px;
    bottom: 84px;
    font-family: "Oswald", sans-serif;
    font-weight: 600;
    font-size: 24px;
    color: var(--ink);
    letter-spacing: 0.5px;
  }
  .services-band {
    position: absolute;
    left: 0; right: 0;
    bottom: 30px;
    height: 40px;
    background: var(--brand-blue);
    display: flex;
    align-items: center;
    justify-content: center;
    gap: 14px;
    font-family: "Oswald", sans-serif;
    font-weight: 500;
    font-size: 18px;
    color: var(--card-white);
    letter-spacing: 0.5px;
  }
  .services-band .sep { font-size: 12px; }
  /* ---------- back ---------- */
  .card-back {
    top: 636px;
    background: radial-gradient(circle at 50% 45%, var(--brand-blue-light) 0%, var(--brand-blue) 45%, var(--brand-blue-deep) 100%);
  }
  .back-mascot {
    position: absolute;
    left: 170px;
    top: 90px;
    width: 300px;
    height: 320px;
    background: linear-gradient(160deg, var(--brand-blue-deep) 0%, var(--brand-blue-deep) 45%, var(--accent-red) 46%, var(--accent-red) 100%);
    border-radius: 6px;
  }
  .brand-name {
    position: absolute;
    left: 500px;
    top: 170px;
    font-weight: 800;
    color: var(--card-white);
    font-size: 40px;
    line-height: 1.1;
    text-transform: uppercase;
  }
</style>
</head>
<body>

<section class="card card-front">
  <div class="front-mascot" role="img" aria-label="Cartoon mascot of a smiling carpet cleaner holding a cleaning wand, on a red square"></div>

  <div class="contact">
    <h1 class="contact-name">FULL NAME</h1>
    <p class="contact-title">TITLE</p>
    <ul class="contact-list">
      <li>
        <svg viewBox="0 0 24 24" aria-hidden="true"><path d="M6.6 10.8a15.1 15.1 0 0 0 6.6 6.6l2.2-2.2a1 1 0 0 1 1-.25 11.4 11.4 0 0 0 3.6.57 1 1 0 0 1 1 1V20a1 1 0 0 1-1 1A17 17 0 0 1 3 4a1 1 0 0 1 1-1h3.5a1 1 0 0 1 1 1c0 1.25.2 2.45.57 3.57a1 1 0 0 1-.25 1z"/></svg>
        (555) 014-2290
      </li>
      <li>
        <svg viewBox="0 0 24 24" aria-hidden="true"><path d="M12 2a10 10 0 1 0 0 20 10 10 0 0 0 0-20zm6.9 6h-2.9a15.6 15.6 0 0 0-1.4-3.6A8 8 0 0 1 18.9 8zM12 4c.8 1.2 1.5 2.5 1.9 4h-3.8c.4-1.5 1.1-2.8 1.9-4zM4.3 14a8 8 0 0 1 0-4h3.4a16.5 16.5 0 0 0 0 4zm.8 2h2.9c.3 1.3.8 2.5 1.4 3.6A8 8 0 0 1 5.1 16zM8 8H5.1a8 8 0 0 1 4.3-3.6C8.8 5.5 8.3 6.7 8 8zm4 12c-.8-1.2-1.5-2.5-1.9-4h3.8c-.4 1.5-1.1 2.8-1.9 4zm2.3-6H9.7a14.7 14.7 0 0 1 0-4h4.6a14.7 14.7 0 0 1 0 4zm.3 5.6c.6-1.1 1.1-2.3 1.4-3.6h2.9a8 8 0 0 1-4.3 3.6zm1.7-5.6a16.5 16.5 0 0 0 0-4h3.4a8 8 0 0 1 0 4z"/></svg>
        www.freshfiberclean.com
      </li>
      <li>
        <svg viewBox="0 0 24 24" aria-hidden="true"><path d="M2 5h20v14H2zm2 2v.5l8 5 8-5V7zm0 2.9V17h16V9.9l-8 5z"/></svg>
        info@freshfiberclean.com
      </li>
    </ul>
  </div>

  <p class="services-label">OUR SERVICES</p>
  <div class="services-band">
    <span>CARPET CLEANING</span><span class="sep">✦</span>
    <span>UPHOLSTERY CLEANING</span><span class="sep">✦</span>
    <span>COMMERCIAL CARPET CLEANING</span><span class="sep">✦</span>
    <span>PET ODOR REMOVAL</span>
  </div>
</section>

<section class="card card-back">
  <div class="back-mascot" role="img" aria-label="Cartoon mascot of a smiling carpet cleaner holding a cleaning wand, on a red square"></div>
  <p class="brand-name">Ray's Fresh<br>Fiber<br>Cleaning</p>
</section>

</body>
</html>
```